Concierge Healthcare Business Card Design and Logo

We need a logo and business card design for a new company called "Sound Haven". We will provide concierge audiological care, hearing aids, hearing exams, custom hearing protection etc to patients in the comfort of their homes and offices. We would like a sleek and modern design preferably with an Ear related logo.

Target Market(s)

People with hearing loss, Hunters, Musicians
My usual clientele are older individuals so usually 50+ years old

Industry/Entity Type

Health Care

Contact Information for Business Card

Celia Brandt, AuD
Audiologist
512-648-2917
soundhaven@mailvoro.com
www.soundhaven-vorel.com

Logo Text

Sound Haven

Number of Pages Required

3 page

```html
<!DOCTYPE html>
<html lang="en">
<head>
<meta charset="utf-8">
<title>Sound Haven – Business Card</title>
<link rel="stylesheet" href="https://fonts.googleapis.com/css2?family=Questrial&family=Montserrat:wght@400;600&display=swap">
<style>
  :root {
    --ink: #000000;
    --paper: #ffffff;
    --brand-blue: #1a78c2;
    --backdrop: #2b2b2b;
    --card-w: 620px;
    --card-h: 354px;
  }
  * { margin: 0; padding: 0; box-sizing: border-box; }
  html, body { width: 1200px; height: 900px; overflow: hidden; }
  body {
    background: var(--backdrop);
    font-family: "Questrial", sans-serif;
    color: var(--paper);
  }
  .canvas {
    position: relative;
    width: 1200px;
    height: 900px;
  }
  .card {
    position: absolute;
    width: var(--card-w);
    height: var(--card-h);
    background: var(--ink);
    border-radius: 22px;
    overflow: hidden;
  }
  /* Front */
  .card--front { left: 150px; top: 56px; }
  .front-mark {
    position: absolute;
    left: 50%;
    top: 58px;
    width: 120px;
    height: 120px;
    margin-left: -60px;
    border: 2px solid var(--paper);
    border-radius: 50%;
  }
  .front-name {
    position: absolute;
    left: 0; right: 0;
    top: 196px;
    text-align: center;
    font-size: 44px;
    letter-spacing: 0.5px;
  }
  .front-web {
    position: absolute;
    left: 0; right: 0;
    top: 272px;
    text-align: center;
    font-family: "Montserrat", sans-serif;
    font-size: 17px;
  }
  .front-web .accent { color: var(--brand-blue); }

  /* Back */
  .card--back { left: 430px; top: 490px; }
  .back-title {
    position: absolute;
    left: 34px;
    top: 28px;
    font-size: 76px;
    line-height: 1;
    letter-spacing: 0.5px;
    white-space: nowrap;
  }
  .back-rule {
    position: absolute;
    left: 250px;
    right: 40px;
    top: 124px;
    height: 1.5px;
    background: var(--brand-blue);
  }
  .back-band {
    position: absolute;
    left: 0; right: 0;
    bottom: 0;
    height: 148px;
    background: var(--brand-blue);
  }
  .back-seal {
    position: absolute;
    right: 24px;
    top: 160px;
    width: 96px;
    height: 96px;
    border-radius: 50%;
    background: var(--ink);
    border: 3px solid var(--paper);
  }
  .person {
    position: absolute;
    left: 70px;
    top: 140px;
    font-family: "Montserrat", sans-serif;
  }
  .person-name {
    color: var(--brand-blue);
    font-weight: 600;
    font-size: 20px;
  }
  .person-role {
    font-size: 16px;
    margin-top: 2px;
  }
  .person-tab {
    position: absolute;
    left: 0;
    top: 150px;
    width: 50px;
    height: 40px;
    background: var(--paper);
    border-right: 10px solid var(--brand-blue);
  }
  .contact-list {
    position: absolute;
    left: 70px;
    bottom: 28px;
    list-style: none;
    font-family: "Montserrat", sans-serif;
    font-size: 16px;
  }
  .contact-list li {
    display: flex;
    align-items: center;
    gap: 12px;
    line-height: 1.55;
  }
  .contact-icon { width: 14px; height: 14px; flex: none; }
</style>
</head>
<body>
<main class="canvas">

  <section class="card card--front" aria-label="Card front">
    <div class="front-mark"></div>
    <div class="front-name">Sound Haven</div>
    <div class="front-web">www.<span class="accent">soundhaven-vorel</span>.com</div>
  </section>

  <section class="card card--back" aria-label="Card back">
    <div class="back-band"></div>
    <div class="back-title">Sound Haven</div>
    <div class="back-rule"></div>
    <div class="back-seal"></div>
    <div class="person-tab"></div>
    <div class="person">
      <div class="person-name">Celia Brandt, AuD</div>
      <div class="person-role">Audiologist</div>
    </div>
    <ul class="contact-list">
      <li>
        <svg class="contact-icon" viewBox="0 0 24 24" fill="#000"><path d="M6.6 10.8a15 15 0 0 0 6.6 6.6l2.2-2.2a1 1 0 0 1 1-.25 11.4 11.4 0 0 0 3.6.57 1 1 0 0 1 1 1V20a1 1 0 0 1-1 1A17 17 0 0 1 3 4a1 1 0 0 1 1-1h3.5a1 1 0 0 1 1 1c0 1.25.2 2.45.57 3.57a1 1 0 0 1-.25 1z"/></svg>
        <span>512-648-2917</span>
      </li>
      <li>
        <svg class="contact-icon" viewBox="0 0 24 24" fill="none" stroke="#000" stroke-width="2.4"><rect x="2" y="5" width="20" height="14" rx="1"/><path d="M2 6l10 7 10-7"/></svg>
        <span>soundhaven@mailvoro.com</span>
      </li>
      <li>
        <svg class="contact-icon" viewBox="0 0 24 24" fill="none" stroke="#000" stroke-width="2.2"><circle cx="12" cy="12" r="10"/><path d="M2 12h20M12 2c3 3 3 17 0 20M12 2c-3 3-3 17 0 20"/></svg>
        <span>www.soundhaven-vorel.com</span>
      </li>
    </ul>
  </section>

</main>
</body>
</html>
```